Business card for my new company (Accounting firm)

I need a business card for my new business Brightwell Advisory and Ledger SA. Our services are accounting, tax, audit and financial management. Our customers are small companies, start-ups and new companies. The final design has to show financial security, trust and growth. Please find our logo attached to the business card. Text for the business card: Brightwell Advisory and Ledger SA Tomas Varenholt Director and Founder Certified Accountant Tel. 022 418 57 34 tv@clairevalconseil.ch www.clairevalconseil.ch Rue des Vergières 27 1201 Geneva
Target Market(s)
Our customers are small companies, start-ups and new companies.
Industry/Entity Type
Finance And Accounting
Contact Information for Business Card
Claireval Conseil et Comptes SA
Tomas Varenholt
Directeur et Fondateur
Expert-comptable diplômé
Tél. 022 418 57 34
tv@clairevalconseil.ch
www.clairevalconseil.ch
Rue des Vergières 27
1201 Genève

```html
<!DOCTYPE html>
<html lang="fr">
<head>
<meta charset="utf-8">
<title>Claireval Conseil et Comptes SA – Carte de visite</title>
<link rel="stylesheet" href="https://fonts.googleapis.com/css2?family=Roboto:wght@400;500;700&display=swap">
<style>
  :root {
    --backdrop: #232222;
    --card-white: #ffffff;
    --navy: #1a6491;
    --sky: #33afe0;
    --ink: #3b3b3b;
    --light-text: #ffffff;
  }
  * { margin: 0; padding: 0; box-sizing: border-box; }
  html, body {
    width: 1125px;
    height: 1200px;
    overflow: hidden;
    background: var(--backdrop);
    font-family: "Roboto", Arial, sans-serif;
  }
  .canvas {
    position: relative;
    width: 1125px;
    height: 1200px;
  }
  .card {
    position: absolute;
    left: 171px;
    width: 826px;
    height: 471px;
    overflow: hidden;
  }
  .card--front { top: 106px; background: var(--card-white); }
  .card--back  { top: 639px; background: var(--sky); }

  .front-panel {
    position: absolute;
    inset: 0;
    width: 826px;
    height: 471px;
  }
  .front-panel path { fill: var(--navy); }

  .contact-block {
    position: absolute;
    left: 40px;
    top: 188px;
    color: var(--light-text);
  }
  .holder-name {
    font-weight: 700;
    font-size: 29px;
    line-height: 34px;
  }
  .holder-role {
    font-size: 20.5px;
    line-height: 27px;
  }
  .address {
    margin-top: 14px;
    font-size: 19.5px;
    line-height: 25px;
  }
  .contact-list {
    list-style: none;
    margin-top: 14px;
    font-size: 19.5px;
    line-height: 26.5px;
  }
  .contact-list li {
    display: flex;
    align-items: center;
    gap: 8px;
  }
  .contact-icon {
    width: 20px;
    height: 20px;
    flex: none;
  }
  .contact-icon * { fill: var(--light-text); }

  .brand-name {
    position: absolute;
    font-weight: 500;
    letter-spacing: 3px;
    white-space: nowrap;
  }
  .card--front .brand-name {
    left: 519px;
    top: 205px;
    font-size: 44px;
    color: var(--ink);
  }
  .card--back .brand-name {
    right: 80px;
    top: 312px;
    font-size: 52px;
    color: var(--light-text);
  }
  .back-website {
    position: absolute;
    right: 80px;
    top: 392px;
    font-size: 17px;
    letter-spacing: 3.4px;
    color: var(--light-text);
  }
</style>
</head>
<body>
<main class="canvas">

  <section class="card card--front" aria-label="Recto de la carte">
    <svg class="front-panel" viewBox="0 0 800 456" preserveAspectRatio="none" aria-hidden="true">
      <path d="M0 0 H214 Q233 0 243 15 L520 456 H0 Z"/>
    </svg>

    <div class="contact-block">
      <h1 class="holder-name">Tomas Varenholt</h1>
      <p class="holder-role">Directeur et Fondateur</p>
      <p class="holder-role">Expert-comptable diplômé</p>

      <p class="address">Rue des Vergières 27<br>1201 Genève</p>

      <ul class="contact-list">
        <li>
          <svg class="contact-icon" viewBox="0 0 24 24" aria-hidden="true">
            <path d="M6.6 10.8c1.4 2.8 3.8 5.1 6.6 6.6l2.2-2.2c.3-.3.7-.4 1-.2 1.1.4 2.3.6 3.6.6.6 0 1 .4 1 1V20c0 .6-.4 1-1 1C10.6 21 3 13.4 3 4c0-.6.4-1 1-1h3.5c.6 0 1 .4 1 1 0 1.3.2 2.5.6 3.6.1.3 0 .7-.2 1l-2.3 2.2z"/>
          </svg>
          <span>022 418 57 34</span>
        </li>
        <li>
          <svg class="contact-icon" viewBox="0 0 24 24" aria-hidden="true">
            <path d="M3 6h18v1.2l-9 5.6-9-5.6z"/>
            <path d="M3 9.2l9 5.6 9-5.6V18H3z"/>
          </svg>
          <span>tv@clairevalconseil.ch</span>
        </li>
        <li>
          <svg class="contact-icon" viewBox="0 0 24 24" aria-hidden="true">
            <path d="M12 2a10 10 0 1 0 0 20 10 10 0 0 0 0-20zm-1 17.9A8 8 0 0 1 4.2 10.8L9 15.6v1a2 2 0 0 0 2 2zm6.9-2.5a2 2 0 0 0-1.9-1.4h-1v-3a1 1 0 0 0-1-1H8v-2h2a1 1 0 0 0 1-1V7h2a2 2 0 0 0 2-2v-.4a8 8 0 0 1 2.9 12.8z"/>
          </svg>
          <span>www.clairevalconseil.ch</span>
        </li>
      </ul>
    </div>

    <p class="brand-name">CLAIREVAL</p>
  </section>

  <section class="card card--back" aria-label="Verso de la carte">
    <p class="brand-name">CLAIREVAL</p>
    <p class="back-website">www.clairevalconseil.ch</p>
  </section>

</main>
</body>
</html>
```